Pepper & Palm Business Card FUN & EXCITING

Here is the Information for the Card:
Jaswinder Bains (Ravi)
E: RaviBains@postlark.com
C: (480) 555-0147
www.PepperPalmLV.com

We don't want traditional Indian cliche, We a playful bold and fun business card.

Files: https://files.cloudvessel.net/share/folders/7TqRmXpZ2vKa9LwBn4YcHd3JsEf6UoGi?usp=share_link

https://files.cloudvessel.net/share/folders/4MzXaQ8rTw2YbNcVk6PsLe5GhJdR3FoU?usp=share_link

Target Market(s)

Las Vegas Local Restaurant

Industry/Entity Type

Indian Restaurant

Contact Information for Business Card

Name, Email, Cell Phone, Company Logo

```html
<!DOCTYPE html>
<html lang="en">
<head>
<meta charset="utf-8">
<title>Pepper &amp; Palm – Business Card</title>
<link href="https://fonts.googleapis.com/css2?family=Montserrat:wght@500;600;800;900&family=Yellowtail&family=Courier+Prime&family=Oswald:wght@300&display=swap" rel="stylesheet">
<style>
  :root {
    --backdrop: #9a9a9a;
    --brand-pink: #cc3559;
    --brand-yellow: #f2c23e;
    --brand-teal: #00b294;
    --paper: #ffffff;
    --ink: #1e1e1e;
    --art-tone: #f3e6c8;
  }
  * { box-sizing: border-box; margin: 0; padding: 0; }
  html, body { width: 1200px; height: 1200px; overflow: hidden; }
  body { background: var(--backdrop); position: relative; font-family: "Montserrat", sans-serif; }

  .card { position: absolute; left: 227px; width: 745px; height: 435px; overflow: hidden; }
  .card--front { top: 91px; background: var(--brand-pink); display: flex; align-items: center; justify-content: center; }
  .card--back { top: 586px; background: var(--paper); }

  .front-name { color: var(--paper); font-weight: 900; font-size: 84px; letter-spacing: -1px; }

  .contact { position: absolute; left: 40px; width: 330px; top: 70px; text-align: center; }
  .contact__name { font-family: "Yellowtail", cursive; color: var(--brand-pink); font-size: 42px; line-height: 52px; }
  .contact__icons { display: flex; justify-content: center; gap: 6px; margin: 14px 0 10px; }
  .contact__icon { width: 32px; height: 32px; border-radius: 50%; background: var(--brand-teal); display: flex; align-items: center; justify-content: center; }
  .contact__line { font-family: "Courier Prime", monospace; font-size: 21px; color: var(--ink); line-height: 28px; }

  .brand-name { position: absolute; left: 440px; width: 270px; top: 38px; text-align: center; color: var(--brand-pink); font-weight: 800; font-size: 28px; }
  .mascot-art { position: absolute; left: 420px; top: 90px; width: 300px; height: 205px; border-radius: 12px;
    background: radial-gradient(ellipse at center, var(--art-tone) 0%, #fbf3e4 70%, var(--paper) 100%); }
  .mascot-tagline { position: absolute; left: 420px; width: 300px; top: 298px; text-align: center; font-family: "Oswald", sans-serif; font-weight: 300; font-size: 16px; color: var(--ink); }

  .quote { position: absolute; left: 0; width: 745px; top: 336px; text-align: center; }
  .quote__text { font-weight: 600; font-size: 21px; color: var(--ink); margin-left: -40px; }
  .quote__source { font-weight: 600; font-size: 12px; color: var(--ink); margin-left: 230px; }

  .info-band { position: absolute; left: 0; bottom: 0; width: 745px; height: 44px; background: var(--brand-teal);
    display: flex; align-items: center; justify-content: center; gap: 14px; color: var(--paper); font-weight: 500; font-size: 19px; }
  .info-band__social { display: flex; gap: 4px; margin-left: 10px; }
  .info-band__dot { width: 15px; height: 15px; background: var(--paper); border-radius: 3px; }
</style>
</head>
<body>
  <section class="card card--front">
    <h1 class="front-name">Pepper &amp; Palm</h1>
  </section>

  <section class="card card--back">
    <div class="contact">
      <p class="contact__name">Jaswinder Bains<br>(Ravi)</p>
      <div class="contact__icons">
        <span class="contact__icon">
          <svg width="14" height="18" viewBox="0 0 14 18"><rect x="2" y="1" width="10" height="16" rx="2" fill="none" stroke="#fff" stroke-width="1.6"/><circle cx="7" cy="14" r="1" fill="#fff"/></svg>
        </span>
        <span class="contact__icon">
          <svg width="18" height="14" viewBox="0 0 18 14"><rect x="1" y="1" width="16" height="12" rx="1" fill="none" stroke="#fff" stroke-width="1.6"/><path d="M1 1 L9 8 L17 1" fill="none" stroke="#fff" stroke-width="1.6"/></svg>
        </span>
      </div>
      <p class="contact__line">(480) 555-0147</p>
      <p class="contact__line">RaviBains@postlark.com</p>
    </div>

    <p class="brand-name">Pepper &amp; Palm</p>
    <div class="mascot-art" role="img" aria-label="Cartoon illustration of a walking curry bowl and naan bread characters with hearts and sparkles"></div>
    <p class="mascot-tagline">“A match made in heaven”</p>

    <div class="quote">
      <p class="quote__text">“Voted Best Indian Restaurant In America”</p>
      <p class="quote__source">— Mom &amp; Dad</p>
    </div>

    <div class="info-band">
      <span>2210 W. Sahara</span>
      <span>|</span>
      <span>pepperpalmlv.com</span>
      <span class="info-band__social"><span class="info-band__dot"></span><span class="info-band__dot"></span><span class="info-band__dot"></span></span>
    </div>
  </section>
</body>
</html>
```